Business card

We need a business card design for our company based in Auckland , New Zealand called 'Ridge + Studio Ltd'. We provide architectural services. We would like to see designs that use the max. three colours (such as white, black, grey) The final design should communicate financial safety and growth."
Also I will provide our company logo. I would like to the logo to be embeded onto our business card.

Target Market(s)

new residential house, alteration & addition & light commericila design & drafting service

Industry/Entity Type

Architecture

Contact Information for Business Card

Company name: ridge + studio Ltd.
Name: Mark Delford
Job title: architectural designer & Design LBP
email address: mark@rplusd.co.nz
mobile number: 02 5163 2290
web site: www.rplusd.co.nz

Requirements
Must have
• My project must have..
• - embeded logo (attached company logo)
• I don't have a bigger version for our company logo, but I have one old one, so you can remove the word from it)
• - insert the attached small BKTW logo & LBP logo
• - creative, simple and clear business card.
• - Max. three colours
Nice to have
• - Here are the samples I would like to share with you: http://www.plimvora.com/blog/minimalistic-business-card-designs/
• I would like to have my business card like one of the creation.
Should not have
• TBA

```html
<!DOCTYPE html>
<html lang="en">
<head>
<meta charset="utf-8">
<title>Ridge + Studio Ltd — Business Card</title>
<link href="https://fonts.googleapis.com/css2?family=PT+Sans:wght@400;700&family=Cinzel:wght@400&display=swap" rel="stylesheet">
<style>
  :root {
    --backdrop: #ecebe8;
    --kraft-light: #c4a77a;
    --kraft-mid: #b8996a;
    --kraft-dark: #a98a5c;
    --ink: #141210;
    --badge-grey: #d9d9d9;
  }
  html, body {
    margin: 0;
    padding: 0;
    overflow: hidden;
  }
  .canvas {
    position: relative;
    width: 1200px;
    height: 900px;
    background: var(--backdrop);
    overflow: hidden;
  }
  .card {
    position: absolute;
    width: 556px;
    height: 342px;
    background: linear-gradient(135deg, var(--kraft-light) 0%, var(--kraft-mid) 55%, var(--kraft-dark) 100%);
    color: var(--ink);
    box-shadow: 0 6px 18px rgba(0, 0, 0, 0.18);
  }
  .card--front {
    left: 238px;
    top: 62px;
  }
  .card--back {
    left: 459px;
    top: 518px;
  }
  .contact {
    position: absolute;
    left: 0;
    right: 0;
    top: 92px;
    text-align: center;
    font-family: "PT Sans", sans-serif;
  }
  .contact__name {
    margin: 0;
    font-size: 22px;
    font-weight: 700;
    letter-spacing: 0.2px;
    line-height: 28px;
  }
  .contact__role {
    margin: 2px 0 0;
    font-size: 16.5px;
    line-height: 22px;
  }
  .contact__details {
    margin: 26px 0 0;
    padding: 0;
    list-style: none;
    font-size: 17.5px;
    line-height: 25px;
  }
  .brand {
    position: absolute;
    left: 0;
    right: 0;
    top: 34px;
    text-align: center;
  }
  .brand__mark {
    display: block;
    margin: 0 auto;
  }
  .brand__name {
    margin: 14px 0 0;
    font-family: "Cinzel", serif;
    font-size: 19px;
    font-weight: 400;
    letter-spacing: 0.4px;
  }
  .badges {
    position: absolute;
    left: 150px;
    top: 206px;
    display: flex;
    align-items: center;
    gap: 22px;
  }
</style>
</head>
<body>
<main class="canvas">
  <section class="card card--front" aria-label="Business card front">
    <div class="contact">
      <h1 class="contact__name">MARK DELFORD</h1>
      <p class="contact__role">Architectural designer &amp; Design LBP</p>
      <ul class="contact__details">
        <li>02 5163 2290</li>
        <li>mark@rplusd.co.nz</li>
        <li>www.rplusd.co.nz</li>
      </ul>
    </div>
  </section>

  <section class="card card--back" aria-label="Business card back">
    <div class="brand">
      <svg class="brand__mark" width="104" height="104" viewBox="0 0 104 104" aria-hidden="true">
        <circle cx="52" cy="52" r="48" fill="none" stroke="var(--ink)" stroke-width="5"/>
      </svg>
      <p class="brand__name">RIDGE + STUDIO LTD.</p>
    </div>
    <div class="badges">
      <svg width="124" height="100" viewBox="0 0 124 100" role="img" aria-label="Professional membership badge">
        <rect x="2" y="2" width="120" height="96" fill="var(--ink)"/>
      </svg>
      <svg width="112" height="112" viewBox="0 0 112 112" role="img" aria-label="Licensed practitioner badge">
        <circle cx="56" cy="56" r="54" fill="var(--badge-grey)" stroke="var(--ink)" stroke-width="4"/>
      </svg>
    </div>
  </section>
</main>
</body>
</html>
```